Award-winnning Estate Agent needs a premium version of their 'For Sale' board design

We need a premium option for our 'For Sale' board design. We have a standard board that is attached to this brief, but were are looking to have a premium design version that we will use when selling exclusive properties. Our company name is Harbourline Vale Estates and the name for this is exclusive selection is: 'The Harbourline Collection'. The design needs to work with our current brand, but have a distinctive PREMIUM feel to it. I have uploaded the barnd guidelines and also some of the exisisting logo variations. We do NOT need a new logo but feel free to play around with colours, fonts, sizes etc. for the sign.

Target Market(s)

Property buyers & house hunters

Industry/Entity Type

Real Estate - Residential Property

Font styles to use
Sans Serif

Requirements
Must have
• A premium fee, must be square design, must be easy to read when driving past the sign
Nice to have
• I'm open ot ideas

```html
<!DOCTYPE html>
<html lang="en">
<head>
<meta charset="utf-8">
<title>For Sale Board – Harbourline Vale Estates</title>
<link rel="stylesheet" href="https://fonts.googleapis.com/css2?family=Montserrat:wght@700;800;900&family=Roboto:wght@500&display=swap">
<style>
  :root {
    --purple: #422a70;
    --brand-blue: #1176bc;
    --accent-blue: #2a9ddc;
    --white: #ffffff;
    --page: #f2f2f2;
  }
  * { margin: 0; padding: 0; box-sizing: border-box; }
  html, body {
    width: 1200px; height: 2389px; overflow: hidden;
    background: var(--page);
  }
  .board {
    position: absolute;
    left: 74px; top: 668px;
    width: 1053px; height: 1053px;
    background: var(--brand-blue);
    box-shadow: 0 6px 14px rgba(0,0,0,0.18);
    overflow: hidden;
    color: var(--white);
    font-family: "Montserrat", sans-serif;
    text-align: center;
  }
  .board__top {
    position: absolute; left: 0; top: 0;
    width: 100%; height: 460px;
    background: var(--purple);
  }
  .board__headline {
    position: absolute; left: 0; top: 46px; width: 100%;
    font-weight: 700; font-size: 178px; line-height: 1;
    letter-spacing: -2px;
  }
  .board__skyline {
    position: absolute; left: 0; top: 267px;
    width: 100%; height: 182px;
    background: linear-gradient(180deg, var(--purple) 0%, #3e5fa6 55%, #6f9fd2 100%);
  }
  .board__skyline-base {
    position: absolute; left: 0; top: 449px;
    width: 100%; height: 11px; background: var(--white);
  }
  .board__company {
    position: absolute; left: 0; top: 478px; width: 100%;
    font-family: "Roboto", sans-serif; font-weight: 500;
    font-size: 52px; line-height: 64px;
  }
  .board__collection {
    position: absolute; left: 73px; top: 560px; width: 907px;
    display: flex; align-items: center; gap: 10px;
    font-weight: 900; font-size: 48px; line-height: 60px;
    letter-spacing: -0.5px; white-space: nowrap;
  }
  .board__collection::before,
  .board__collection::after {
    content: ""; flex: 1; height: 4px; background: var(--white);
  }
  .board__divider {
    position: absolute; left: 165px; width: 723px; height: 68px;
  }
  .board__divider--phone { top: 636px; }
  .board__divider--web { top: 845px; }
  .board__phone {
    position: absolute; left: 0; top: 712px; width: 100%;
    font-weight: 700; font-size: 124px; line-height: 126px;
    letter-spacing: -2px;
  }
  .board__web {
    position: absolute; left: 0; top: 924px; width: 100%;
    font-weight: 700; font-size: 40px; line-height: 52px;
  }
</style>
</head>
<body>
  <section class="board" aria-label="For sale board">
    <div class="board__top"></div>
    <h1 class="board__headline">FOR SALE</h1>
    <div class="board__skyline" role="img" aria-label="Stylised town skyline with a tower and rooftops"></div>
    <div class="board__skyline-base"></div>

    <p class="board__company">Harbourline Vale Estates</p>
    <p class="board__collection">THE HARBOURLINE COLLECTION</p>

    <svg class="board__divider board__divider--phone" viewBox="0 0 723 68" aria-hidden="true">
      <rect x="0" y="32" width="723" height="4" fill="var(--accent-blue)"/>
      <circle cx="361.5" cy="34" r="34" fill="var(--accent-blue)"/>
      <path d="M349 20c2-2 5-2 6 0l4 6c1 2 0 4-1 5l-2 2c2 5 6 9 11 11l2-2c1-1 3-2 5-1l6 4c2 1 2 4 0 6l-3 3c-3 2-7 2-11 0-9-5-16-12-21-21-2-4-2-8 0-11z" fill="var(--white)"/>
      <path d="M366 22a12 12 0 0 1 10 10M366 15a19 19 0 0 1 17 17" stroke="var(--white)" stroke-width="3" fill="none" stroke-linecap="round"/>
    </svg>

    <p class="board__phone">01632960418</p>

    <svg class="board__divider board__divider--web" viewBox="0 0 723 68" aria-hidden="true">
      <rect x="0" y="32" width="723" height="4" fill="var(--accent-blue)"/>
      <circle cx="361.5" cy="34" r="34" fill="var(--accent-blue)"/>
      <circle cx="361.5" cy="34" r="20" fill="none" stroke="var(--white)" stroke-width="3"/>
      <ellipse cx="361.5" cy="34" rx="9" ry="20" fill="none" stroke="var(--white)" stroke-width="3"/>
      <path d="M341.5 34h40M345 24h33M345 44h33" stroke="var(--white)" stroke-width="3"/>
    </svg>

    <p class="board__web">www.harbourlinevaleestates.co.uk</p>
  </section>
</body>
</html>
```